Indy Film Production Company/Studio

We need a business card designed from an existing logo. We are a digital studio/production company that caters to creating genre entertainment, like Action, Horror, and martial arts. The card along with the logo will be used to Brand the company from letter heads to banners. The design will also be used for postcards and Brochures. It should be professional and masculine.
Updates

Thank you to all the designers who have participated. I'm narrowing down who it will be. Thank you again.

Target Market(s)

Investors, Networks, Producers, and actors

Industry/Entity Type

Film Production

Contact Information for Business Card

Teodoro Valbuena
Producer/Writer/Director
www.kestrelpicturehouse.example

Requirements
Must have
• Website address, Facebook icon and Twitter icon possibly in the back of the card.
Nice to have
• Logline of Company: Follow The Action.

```html
<!DOCTYPE html>
<html lang="en">
<head>
<meta charset="utf-8">
<title>Kestrel Picture House – Business Card</title>
<link href="https://fonts.googleapis.com/css2?family=Source+Sans+3:ital,wght@0,400;0,600;0,800;1,400&display=swap" rel="stylesheet">
<style>
  :root {
    --stage: #3a3a3a;
    --card-white: #f7f7f7;
    --brand-red: #e31b23;
    --ink: #222222;
    --ink-soft: #4a4a4a;
    --rule: #9a9a9a;
    --band-dark: #2e2e2e;
    --white: #ffffff;
  }
  html, body {
    margin: 0;
    padding: 0;
    width: 1200px;
    height: 750px;
    overflow: hidden;
    background: var(--stage);
    font-family: "Source Sans 3", "Myriad Pro", Arial, sans-serif;
  }
  .stage {
    position: relative;
    width: 1200px;
    height: 750px;
  }
  .card {
    position: absolute;
    left: 371px;
    width: 462px;
    height: 263px;
    overflow: hidden;
    box-shadow: 0 4px 10px rgba(0,0,0,0.45);
  }
  /* Front */
  .card-front {
    top: 81px;
    background: var(--card-white);
  }
  .brand-mark {
    position: absolute;
    right: 26px;
    top: 44px;
    text-align: right;
    color: var(--brand-red);
    font-weight: 800;
    text-transform: uppercase;
    font-size: 21px;
    line-height: 1.05;
    letter-spacing: 0.5px;
  }
  .person {
    position: absolute;
    left: 21px;
    top: 139px;
  }
  .person-name {
    margin: 0;
    color: var(--brand-red);
    font-weight: 600;
    font-size: 19px;
    line-height: 1.1;
  }
  .person-role {
    margin: 2px 0 0;
    color: var(--ink);
    font-size: 13px;
  }
  .divider {
    position: absolute;
    left: 21px;
    right: 21px;
    top: 181px;
    height: 1px;
    background: var(--rule);
  }
  .contact-list {
    position: absolute;
    left: 21px;
    top: 189px;
    margin: 0;
    padding: 0;
    list-style: none;
    color: var(--ink-soft);
    font-size: 12.5px;
  }
  .contact-list li {
    display: flex;
    align-items: center;
    height: 17.5px;
  }
  .contact-list svg {
    width: 12px;
    height: 12px;
    margin-right: 7px;
    fill: var(--brand-red);
  }
  .social {
    position: absolute;
    right: 21px;
    top: 212px;
    display: flex;
    gap: 4px;
  }
  .social span {
    width: 23px;
    height: 23px;
    background: var(--brand-red);
  }
  .band {
    position: absolute;
    left: 0;
    right: 0;
    bottom: 0;
    height: 9px;
  }
  /* Back */
  .card-back {
    top: 382px;
    background: var(--brand-red);
  }
  .camera-photo {
    position: absolute;
    left: 0;
    top: 0;
    width: 282px;
    height: 100%;
    background: linear-gradient(100deg, rgba(20,20,20,0.95) 0%, rgba(40,40,40,0.9) 70%, rgba(227,27,35,0) 100%);
  }
  .back-brand {
    position: absolute;
    right: 18px;
    top: 168px;
    text-align: right;
    color: var(--white);
  }
  .back-brand .brand-name {
    font-weight: 800;
    text-transform: uppercase;
    font-size: 21px;
    line-height: 1.05;
    letter-spacing: 0.5px;
  }
  .back-brand .brand-url {
    margin-top: 8px;
    font-style: italic;
    font-size: 13px;
  }
</style>
</head>
<body>
<main class="stage">

  <section class="card card-front" aria-label="Business card front">
    <div class="brand-mark">Kestrel<br>Picture House</div>

    <div class="person">
      <h1 class="person-name">Teodoro Valbuena</h1>
      <p class="person-role">Producer/Writer/Director</p>
    </div>

    <div class="divider"></div>

    <ul class="contact-list">
      <li>
        <svg viewBox="0 0 24 24" aria-hidden="true"><path d="M6.6 10.8a15.1 15.1 0 0 0 6.6 6.6l2.2-2.2a1 1 0 0 1 1-.25 11.4 11.4 0 0 0 3.6.57 1 1 0 0 1 1 1V20a1 1 0 0 1-1 1A17 17 0 0 1 3 4a1 1 0 0 1 1-1h3.5a1 1 0 0 1 1 1c0 1.25.2 2.45.57 3.6a1 1 0 0 1-.25 1z"/></svg>
        555 014 2290
      </li>
      <li>
        <svg viewBox="0 0 24 24" aria-hidden="true"><path d="M2 5h20v14H2z M2 5l10 8 10-8" fill-rule="evenodd"/><path d="M3 6l9 7 9-7" fill="none" stroke="#f7f7f7" stroke-width="1.6"/></svg>
        hello@kestrelpicturehouse.example
      </li>
      <li>
        <svg viewBox="0 0 24 24" aria-hidden="true"><circle cx="12" cy="12" r="10"/><path d="M2 12h20M12 2c3 3 3 17 0 20M12 2c-3 3-3 17 0 20" fill="none" stroke="#f7f7f7" stroke-width="1.5"/></svg>
        www.kestrelpicturehouse.example
      </li>
    </ul>

    <div class="social" aria-label="Social media">
      <span></span><span></span>
    </div>

    <svg class="band" viewBox="0 0 462 9" preserveAspectRatio="none" aria-hidden="true">
      <polygon points="0,0 300,0 297,9 0,9" fill="var(--brand-red)"/>
      <polygon points="302,0 462,0 462,9 299,9" fill="var(--band-dark)"/>
    </svg>
  </section>

  <section class="card card-back" aria-label="Business card back">
    <div class="camera-photo" role="img" aria-label="Photograph of a professional digital cinema camera rig with monitor and matte box"></div>
    <div class="back-brand">
      <div class="brand-name">Kestrel<br>Picture House</div>
      <div class="brand-url">www.kestrelpicturehouse.example</div>
    </div>
  </section>

</main>
</body>
</html>
```